Label Design for Climbing Chalk (fitness category)

I am looking for someone to design a front and back label for a bottle of liquid chalk. Liquid chalk is used in gyms, gymnastics, climbing to prevent your hands from getting moist and increase friction. I'm uploading some design motivations that I like.

The bottle is going to be black and I want the label to be clear. You have free reign of how you want to approach this design. Below are more specifics for the sizing:

*Attached is a picture of a competitor product (Tor Hold Liquid Chalk). Please don't use this for motivation, their label is very bad. I'm attaching a picture so that you can see what the bottle looks like.
*Attached are design motivations that I like
*The bottle is 50 ml, it's 3.75 inches tall, 2 inches wide and 1.25 inches in depth.
*The label can be square or oval (it's up to you). The size of the label needs to be 1,25 x 2.25 inches.
*Name of the product: Bravan Liquid Chalk
*Label needs to have the following Required Text. You can arrange it however you like:
- (50 ml)
- Made by USA Competitive Athletes for Athletes. Increases grip and lasts 3-4 times longer than regular chalk.
- Directions: Shake well. Squeeze some Bravan Liquid Chalk into your hand and rub your hands together. Let your hands air dry for about 10 seconds. To remove the chalk wash your hands with light soap.
Warning: Avoid contact with Eyes. Do not use on broken skin. Do not ingest. Keep out of reach of small children.
- Ingredients: Magnesium carbonate, SD Alcohol, hydroxypropylcellulose, colophonium.

Target Market(s)

Fitness, Athletes, Rock Climbers, Weight Lifters, Gymnasts, etc

Industry/Entity Type

Fitness

Font styles to use
Sans Serif

Colors

Designer to choose colors to be used in the design.

Requirements
Must have
• Please see Project Description for required text. The bottle is going to be black and I want the clear label so please be creative with the colors that would look good
Nice to have
• Please see attached branding ideas that I liked for font and colors. You don't have to strictly stick to them, these are just some of the ones I liked. Be creative and put your best foot forward.

```html
<!DOCTYPE html>
<html lang="en">
<head>
<meta charset="utf-8">
<title>Bravan Liquid Chalk – Front and Back Labels</title>
<link rel="stylesheet" href="https://fonts.googleapis.com/css2?family=Figtree:ital,wght@0,400;0,500;0,800;1,400;1,500;1,700;1,800&family=Barlow+Semi+Condensed:wght@700&display=swap">
<style>
  :root {
    --navy: #15213a;
    --navy-deep: #141a33;
    --rust: #c9623b;
    --white: #f5f5f3;
    --ink: #111111;
    --page: #ffffff;
  }
  html, body {
    margin: 0;
    padding: 0;
    width: 1200px;
    height: 1029px;
    overflow: hidden;
    background: var(--page);
  }
  .canvas {
    position: relative;
    width: 1200px;
    height: 1029px;
    overflow: hidden;
    font-family: "Figtree", sans-serif;
  }
  .label {
    position: absolute;
    background: var(--white);
    border-radius: 9999px;
    box-shadow: 14px 22px 30px rgba(0, 0, 0, 0.28);
  }
  .label__band {
    position: absolute;
    inset: 9px;
    background: var(--navy);
    border-radius: 9999px;
  }
  .label__field {
    position: absolute;
    background: var(--rust);
    border-radius: 9999px;
    overflow: hidden;
  }
  /* Front label */
  .label--front { left: 140px; top: 118px; width: 432px; height: 767px; }
  .label--front .label__field { left: 30px; top: 52px; width: 372px; height: 679px; }
  .hand-art {
    position: absolute;
    left: -6px;
    top: 185px;
    width: 388px;
    height: 500px;
    background: var(--navy-deep);
    border-radius: 60px 60px 170px 170px;
  }
  .front__brand {
    position: absolute;
    left: 0; right: 0;
    top: 74px;
    text-align: center;
    font-weight: 800;
    font-size: 104px;
    line-height: 1;
    color: var(--white);
  }
  .front__product {
    position: absolute;
    left: 0; right: 0;
    top: 268px;
    text-align: center;
    font-family: "Barlow Semi Condensed", sans-serif;
    font-weight: 700;
    font-size: 56px;
    line-height: 1;
    color: var(--white);
  }
  .front__claim {
    position: absolute;
    left: 95px;
    width: 230px;
    top: 476px;
    margin: 0;
    text-align: center;
    font-style: italic;
    font-size: 17.5px;
    line-height: 21px;
    letter-spacing: 0.06em;
    color: var(--white);
  }
  .front__volume {
    position: absolute;
    left: 0; right: 0;
    top: 608px;
    text-align: center;
    font-style: italic;
    font-size: 33px;
    letter-spacing: 0.04em;
    color: var(--white);
  }
  /* Back label */
  .label--back { left: 640px; top: 126px; width: 436px; height: 774px; }
  .label--back .label__field { left: 36px; top: 36px; width: 364px; height: 703px; }
  .back__brand {
    position: absolute;
    left: 0; right: 0;
    top: 46px;
    text-align: center;
    font-weight: 800;
    font-size: 70px;
    line-height: 1;
    color: var(--white);
  }
  .back__product {
    position: absolute;
    left: 0; right: 0;
    top: 140px;
    text-align: center;
    font-family: "Barlow Semi Condensed", sans-serif;
    font-weight: 700;
    font-size: 40px;
    line-height: 1;
    color: var(--ink);
    -webkit-text-stroke: 0;
    text-shadow: 2px 0 0 var(--white), -2px 0 0 var(--white), 0 2px 0 var(--white), 0 -2px 0 var(--white),
                 2px 2px 0 var(--white), -2px -2px 0 var(--white), 2px -2px 0 var(--white), -2px 2px 0 var(--white);
  }
  .back__section {
    position: absolute;
    left: 20px;
    width: 336px;
  }
  .back__heading {
    margin: 0;
    font-style: italic;
    font-weight: 800;
    font-size: 22px;
    line-height: 26px;
    letter-spacing: 0.02em;
    color: var(--white);
  }
  .back__text {
    margin: 0;
    font-size: 17.5px;
    line-height: 24px;
    letter-spacing: 0.06em;
    color: var(--ink);
  }
  .back__section--directions { top: 200px; }
  .back__section--warning { top: 388px; }
  .back__rule {
    position: absolute;
    left: 48px;
    top: 515px;
    width: 274px;
    height: 8px;
    background: var(--navy);
  }
  .back__section--ingredients {
    top: 555px;
    left: 0;
    width: 364px;
    text-align: center;
  }
  .back__section--ingredients .back__heading { font-size: 20px; line-height: 24px; }
  .back__section--ingredients .back__text {
    font-style: italic;
    font-size: 17.5px;
    line-height: 24px;
    letter-spacing: 0.04em;
  }
</style>
</head>
<body>
<main class="canvas">

  <section class="label label--front" aria-label="Front label">
    <div class="label__band"></div>
    <div class="label__field">
      <div class="hand-art" role="img" aria-label="Dark navy silhouette of an open hand with spread fingers"></div>
      <div class="front__brand">Bravan</div>
      <div class="front__product">LIQUID CHALK</div>
      <p class="front__claim">Made by USA Competitive Athletes for Athletes. Increases grip and lasts 3-4 times longer than regular chalk.</p>
      <div class="front__volume">50 ml</div>
    </div>
  </section>

  <section class="label label--back" aria-label="Back label">
    <div class="label__band"></div>
    <div class="label__field">
      <div class="back__brand">Bravan</div>
      <div class="back__product">LIQUID CHALK</div>

      <div class="back__section back__section--directions">
        <h2 class="back__heading">Directions:</h2>
        <p class="back__text">Shake well. Squeeze some Bravan Liquid Chalk into your hand and rub your hands together. Let your hands air dry for about 10 seconds. To remove the chalk wash your hands with light soap.</p>
      </div>

      <div class="back__section back__section--warning">
        <h2 class="back__heading">Warning:</h2>
        <p class="back__text">Avoid contact with Eyes. Do not use on broken skin. Do not ingest. Keep out of reach of small children.</p>
      </div>

      <div class="back__rule"></div>

      <div class="back__section back__section--ingredients">
        <h2 class="back__heading">Ingredients:</h2>
        <p class="back__text">Magnesium carbonate, SD Alcohol,<br>hydroxypropylcellulose,<br>colophonium.</p>
      </div>
    </div>
  </section>

</main>
</body>
</html>
```